Dorrow Hollow Ranch all natural beef packaging

I would like a custom label to affix to my packages of steaks, roasts, and burgers. The packaging label should be simple and represent the all natural, healthy and humane way we raise our grass finished and natural grain finished beef. check out www.dorrowhollowranch.example for photos of the ranch and information about our cattle.

Target Market(s)

consumers who wish to purchase beef that is born and raised in Ohio, never given any antibiotics, implants, or hormones. Cattle are never confined, always on pasture, even when finished on grain. Humane treatment of the animals which are handled by horseback and on foot.

Industry/Entity Type

Ranch

Requirements
Must have
• Must be able to incorporate the Prairie Forage Alliance label.
• http://www.prairieforagealliance.example/
• I like dark colors, rich and earthy, but maybe on a white background to stand out on the clear plastic wrap over the beef. Imagine you're buying a steak at Halvins and look at how the packaging stands off from the color of the meat.
Nice to have
• I would like a very simple label that incorporates some icon or picture of a calf or cow. See my website www.dorrowhollowranch.example

```html
<!DOCTYPE html>
<html lang="en">
<head>
<meta charset="utf-8">
<title>Dorrow Hollow Ranch – Beef Label</title>
<link href="https://fonts.googleapis.com/css2?family=Oswald:wght@400;500&display=swap" rel="stylesheet">
<style>
  :root {
    --backdrop: #231f20;
    --ink-light: #ffffff;
    --label-cream: #e4d9a9;
    --label-green: #1b6b4b;
    --label-ink: #1a1a1a;
  }
  html, body {
    margin: 0;
    padding: 0;
    width: 800px;
    height: 1200px;
    overflow: hidden;
    background: var(--backdrop);
  }
  .canvas {
    position: relative;
    width: 800px;
    height: 1200px;
    background: var(--backdrop);
    font-family: "Oswald", "Arial Narrow", sans-serif;
  }
  .brand-lockup {
    position: absolute;
    top: 190px;
    left: 0;
    width: 800px;
    display: flex;
    align-items: center;
    justify-content: center;
    gap: 22px;
  }
  .brand-lockup__dot {
    width: 70px;
    height: 70px;
    border: 4px solid var(--ink-light);
    border-radius: 50%;
    box-sizing: border-box;
  }
  .brand-lockup__name {
    margin: 0;
    color: var(--ink-light);
    font-weight: 500;
    font-size: 50px;
    letter-spacing: 1px;
  }
  .package-label {
    position: absolute;
    left: 80px;
    top: 520px;
    width: 640px;
    height: 380px;
    filter: drop-shadow(0 6px 10px rgba(0,0,0,0.5));
  }
  .package-label__text { font-family: "Oswald", "Arial Narrow", sans-serif; fill: var(--label-ink); }
  .package-label__name { font-family: "Oswald", "Arial Narrow", sans-serif; font-weight: 500; fill: var(--label-green); }
</style>
</head>
<body>
<main class="canvas">
  <header class="brand-lockup">
    <span class="brand-lockup__dot"></span>
    <h1 class="brand-lockup__name">Dorrow Hollow Ranch</h1>
  </header>

  <svg class="package-label" viewBox="0 0 640 380" xmlns="http://www.w3.org/2000/svg">
    <defs>
      <path id="label-bottom-arc" d="M 44 196 A 276 164 0 0 0 596 196"/>
    </defs>
    <ellipse cx="320" cy="190" rx="313" ry="183" fill="var(--label-cream)" stroke="var(--label-green)" stroke-width="12"/>

    <circle cx="180" cy="96" r="20" fill="var(--label-green)"/>
    <text class="package-label__name" x="212" y="107" font-size="30">Dorrow Hollow Ranch</text>

    <circle class="package-label__partner-badge" cx="100" cy="196" r="50" fill="var(--label-green)" role="img" aria-label="Prairie Forage Alliance certification badge"/>

    <rect class="package-label__inspection-badge" role="img" aria-label="State inspection seal"
          x="500" y="144" width="64" height="64" rx="6"
          fill="none" stroke="var(--label-ink)" stroke-width="2.5"/>

    <g class="package-label__text" text-anchor="middle">
      <text x="320" y="196" font-size="22" font-weight="500">Lorem ipsum dolor</text>
      <text x="320" y="221" font-size="18">sit amet, consectetur</text>
      <text x="320" y="244" font-size="18">adipiscing elit, sed do</text>
      <text x="320" y="267" font-size="18">eiusmod tempor</text>
      <text x="320" y="290" font-size="18">incididunt ut labore et</text>
    </g>

    <text class="package-label__text" font-size="15" font-weight="500">
      <textPath href="#label-bottom-arc" startOffset="50%" text-anchor="middle">sit amet, consectetur adipiscing elit, sed do eiusmod tempor incididunt ut labore et</textPath>
    </text>
  </svg>
</main>
</body>
</html>
```